New Business Card for Web Design/Internet Marketing Company

Looking for a great looking new business card. We are a 10 year old web design, internet marketing and website management company that works mostly with small businesses.

Our new card needs to better match the colors and style of our website, be bold, extremely usable and slightly edgy.

Target Market(s)

Small/Medium businesses that have websites

Industry/Entity Type

Internet

Requirements
Must have
• Front and back design, full color, rounded corners please

Must use the colors/style of our website (JPG provided)

INFO FOR CARDS (as readable as possible please)
Mark Lenner
President/CEO
mark@trelvanmedia.example
Phone: 520-381-7459
Toll Free: 866-381-7459
Address: 4315 W. Calloway Ave. Ste. 140, Tucson, AZ 85792

THINGS I WANT TO PROMOTE (if there is room):
1. Our Website - www.trelvanmedia.example

2. Social Media
Twitter: @trelvanmedia
Facebook: www.facebook.com/trelvanmedia

3. Our Services
Web Design
Internet Marketing
Website Management

```html
<!DOCTYPE html>
<html lang="en">
<head>
<meta charset="utf-8">
<title>Trelvan Media – Business Card</title>
<link rel="stylesheet" href="https://fonts.googleapis.com/css2?family=Cabin:wght@400;600;700&display=swap">
<style>
  :root {
    --navy: #233e6f;
    --sky: #1b8ccc;
    --orange: #f39322;
    --grey: #6d6e71;
    --white: #ffffff;
    --mark: #6fa7d8;
    --backdrop: #e8e5e1;
    --radius: 14px;
  }
  html, body {
    margin: 0;
    width: 1200px;
    height: 402px;
    overflow: hidden;
    background: var(--backdrop);
    font-family: "Cabin", Arial, sans-serif;
  }
  .canvas { position: relative; width: 1200px; height: 402px; }
  .card {
    position: absolute;
    top: 56px;
    width: 512px;
    height: 290px;
    border-radius: var(--radius);
    overflow: hidden;
  }
  .card--front { left: 62px; background: var(--white); }
  .card--back { left: 626px; background: var(--navy); color: var(--white); }

  .front-shapes { position: absolute; inset: 0; }

  .brand {
    position: absolute;
    left: 40px;
    top: 58px;
    display: flex;
    align-items: center;
    gap: 12px;
  }
  .brand__dot { width: 26px; height: 26px; border-radius: 50%; background: var(--orange); }
  .brand__name { font-size: 46px; font-weight: 700; color: var(--sky); letter-spacing: -0.5px; line-height: 1; }

  .person {
    position: absolute;
    right: 306px;
    top: 218px;
    text-align: right;
    color: var(--white);
  }
  .person__name { font-size: 17px; font-weight: 700; margin: 0; }
  .person__title { font-size: 12px; margin: 2px 0 0; }
  .divider {
    position: absolute;
    left: 241px;
    top: 190px;
    width: 1px;
    height: 94px;
    background: var(--white);
  }
  .contact {
    position: absolute;
    left: 271px;
    top: 189px;
    margin: 0;
    padding: 0;
    list-style: none;
    color: var(--white);
    font-size: 12.5px;
    line-height: 17.5px;
  }
  .contact li { display: flex; align-items: center; gap: 6px; white-space: nowrap; }
  .contact svg { width: 9px; height: 9px; flex: none; }
  .contact .contact__address { display: block; margin-top: 3px; line-height: 14px; }

  .social {
    position: absolute;
    left: 274px;
    top: 38px;
    margin: 0;
    padding: 0;
    list-style: none;
    font-size: 16px;
    line-height: 24px;
  }
  .social li { display: flex; align-items: center; gap: 10px; }
  .social__mark { width: 16px; height: 16px; border-radius: 3px; background: var(--mark); }
  .back-brand {
    position: absolute;
    left: 30px;
    top: 178px;
    font-size: 30px;
    font-weight: 700;
    line-height: 1;
    white-space: nowrap;
  }
  .services {
    position: absolute;
    left: 272px;
    top: 162px;
    margin: 0;
    padding: 0;
    list-style: none;
    font-size: 22px;
    line-height: 32px;
    white-space: nowrap;
  }
</style>
</head>
<body>
<main class="canvas">
  <section class="card card--front" aria-label="Card front">
    <svg class="front-shapes" viewBox="0 0 512 290" width="512" height="290" aria-hidden="true">
      <path d="M0 146 Q256 178 512 138 L512 152 Q256 196 0 166 Z" fill="var(--grey)"/>
      <path d="M0 166 Q256 196 512 152 L512 290 L0 290 Z" fill="var(--navy)"/>
      <path d="M150 180 L174 182 L160 196 Z" fill="var(--white)"/>
    </svg>

    <div class="brand">
      <span class="brand__dot"></span>
      <span class="brand__name">Trelvan Media</span>
    </div>

    <div class="person">
      <p class="person__name">Mark Lenner</p>
      <p class="person__title">President/CEO</p>
    </div>
    <div class="divider"></div>
    <ul class="contact">
      <li><svg viewBox="0 0 10 10"><circle cx="5" cy="5" r="4.5" fill="none" stroke="#fff"/><path d="M3 3 L4.5 3 L4 4.5 L5.5 6 L7 5.5 L7 7 Q4 8 3 3Z" fill="#fff"/></svg>520-381-7459</li>
      <li><svg viewBox="0 0 10 10"><circle cx="5" cy="5" r="4.5" fill="none" stroke="#fff"/><path d="M3 3 L4.5 3 L4 4.5 L5.5 6 L7 5.5 L7 7 Q4 8 3 3Z" fill="#fff"/></svg>866-381-7459</li>
      <li><svg viewBox="0 0 10 10"><rect x="0.5" y="2" width="9" height="6" fill="#fff"/><path d="M0.5 2 L5 5.5 L9.5 2" fill="none" stroke="var(--navy)"/></svg>mark@trelvanmedia.example</li>
      <li><svg viewBox="0 0 10 10"><circle cx="5" cy="5" r="4.5" fill="#fff"/><path d="M0.5 5 H9.5 M5 0.5 V9.5" stroke="var(--navy)" stroke-width="0.8"/></svg>www.trelvanmedia.example</li>
      <li class="contact__address">4315 W. Calloway Ave., Ste. 140<br>Tucson, AZ 85792</li>
    </ul>
  </section>

  <section class="card card--back" aria-label="Card back">
    <ul class="social">
      <li><span class="social__mark"></span>@trelvanmedia</li>
      <li><span class="social__mark"></span>trelvanmedia</li>
    </ul>
    <div class="back-brand">Trelvan Media</div>
    <ul class="services">
      <li>Web Design</li>
      <li>Internet Marketing</li>
      <li>Website Management</li>
    </ul>
  </section>
</main>
</body>
</html>
```